Product Description page for Hullwrap.com, References here just need a clean up redesign

Hi, were working on updating the product description page of our site hullwrap.com

Attached is a reference of what we drew on paint. We want to keep it pretty much the same as far as whats on there, the components with a few small adjustments and a clean actually designed look.

1. We want to remove the tabs (product description, warranty, reviews) and put it all in that main content area stretching down into sections. IE: Product Description section, followed by reviews, followed by warranty, below each other.
2. The side bar needs to be redesigned as far as the look and feel but the content and whats in there should stay the same.
3. The main banner area will be replaced shortly you do not have to worry about that.
4. Include a section or box for people to put in their email for a free Ebook.

Target Market(s)

people looking to easily view our boat cover products and buy without having to click too often or leave the page.

Industry/Entity Type

Online Shopping

Number of Pages Required

1 page

Requirements
Must have
• - Must update the sidebar
• - Must update the content area to remove the tabs and put the content from each tab sectioned off below each other (dummy text is fine for now for the tabs you cant view)
Nice to have
• - Cool place thats clean and functional to insert a section for people to put in their email to receive a free ebook
Should not have
• - too much change, we already know what we want and have a solid reference to work from.

```html
<!DOCTYPE html>
<html lang="en">
<head>
<meta charset="utf-8">
<title>Hullwrap.com – Center Console Boat Cover</title>
<link href="https://fonts.googleapis.com/css2?family=Open+Sans:wght@400;600;700;800&display=swap" rel="stylesheet">
<style>
:root{
  --blue:#1f63b0;
  --blue-dark:#173a66;
  --navy:#12304f;
  --green:#3bb04a;
  --red:#e0322b;
  --star:#f5a623;
  --text:#3a3f47;
  --muted:#8a919b;
  --line:#dde2e8;
  --panel:#eef1f5;
  --bar:#e3e7ec;
  --white:#ffffff;
}
*{box-sizing:border-box;margin:0;padding:0}
html,body{width:889px;height:1200px;overflow:hidden}
body{font-family:"Open Sans",Arial,sans-serif;color:var(--text);background:var(--white);position:relative;font-size:9px}
.abs{position:absolute}

/* header */
.brand{left:124px;top:12px;display:flex;align-items:center;gap:6px}
.brand-mark{width:14px;height:14px;background:var(--blue)}
.brand-name{font-size:19px;font-weight:800;color:var(--blue);letter-spacing:.3px}
.contact{right:124px;top:8px;text-align:right}
.contact-phone{display:flex;align-items:center;gap:5px;font-size:17px;font-weight:700;color:var(--blue)}
.contact-hours{font-size:8px;color:var(--muted)}
.nav{left:124px;top:44px;width:641px;height:22px;background:var(--bar);display:flex;align-items:center;padding-left:4px}
.nav a{font-size:8.5px;color:var(--blue-dark);text-decoration:none;padding:0 12px;border-right:1px solid #c9d0d8;line-height:22px}
.nav .checkout{margin-left:auto;background:var(--blue);color:var(--white);font-weight:700;height:22px;display:flex;align-items:center;gap:5px;padding:0 12px;font-size:8.5px}
.crumbs{left:124px;top:76px;width:641px;height:16px;background:var(--navy);color:#c8d6e6;font-size:7.5px;line-height:16px;padding-left:10px}

/* scene */
.scene{left:0;top:872px;width:889px;height:156px;background:linear-gradient(180deg,#d9e9f5 0%,#a9cde8 30%,#5d9cc8 52%,#2f6f9c 74%,#d9cfb0 90%,#c9bc98 100%)}

/* page body */
.sheet{left:124px;top:92px;width:641px;height:808px;background:var(--white)}
.gallery-main{left:133px;top:100px;width:312px;height:196px;background:radial-gradient(ellipse at 50% 55%,#c4c9cf 0%,#e8ebee 55%,#ffffff 80%)}
.thumbs{left:133px;top:306px;display:flex;gap:5px}
.thumb{width:40px;height:38px;background:linear-gradient(135deg,#cbd6e2,#6f8db0);border:1px solid var(--line)}
.thumb.active{border:2px solid var(--blue)}

.buy{left:459px;top:100px;width:306px}
.buy h1{font-size:12.5px;line-height:15px;font-weight:700;color:var(--blue)}
.rating{display:flex;align-items:center;gap:4px;margin-top:6px;color:var(--star);font-size:10px}
.rating span{color:var(--muted);font-size:7.5px}
.was{margin-top:6px;font-size:7.5px;color:var(--muted);text-decoration:line-through}
.sale{font-size:7.5px;color:var(--muted)}
.sale b{color:var(--red)}
.price{font-size:19px;font-weight:800;color:var(--red);margin-top:2px}
.field{display:flex;align-items:center;gap:8px;margin-top:9px}
.field label{width:48px;text-align:right;font-size:8px;font-weight:600}
.select{flex:1;height:17px;border:1px solid var(--line);font-size:7.5px;color:var(--muted);line-height:15px;padding-left:5px;position:relative}
.select:after{content:"";position:absolute;right:6px;top:6px;border:3px solid transparent;border-top-color:var(--muted)}
.cart{margin-top:10px;margin-left:56px;height:29px;background:var(--green);color:var(--white);font-weight:700;font-size:13px;display:flex;align-items:center;justify-content:center}
.share{margin-top:7px;margin-left:56px;display:flex;gap:4px}
.share i{width:12px;height:12px;border-radius:2px;background:#b9c3ce;display:block}

/* info column: stacked sections */
.info{left:124px;top:378px;width:365px}
.section + .section{margin-top:8px}
.section-bar{height:17px;background:var(--bar);display:flex;align-items:center;gap:6px;padding-left:8px;font-size:8px;font-weight:600;color:var(--blue-dark)}
.section-bar:before{content:"";width:7px;height:7px;border-radius:50%;background:#9aa5b2}
.section-body{padding:8px 8px 0 8px}
.info h2{font-size:8.5px;font-weight:700;color:var(--text);margin-bottom:4px}
.info p{font-size:7px;line-height:10px;color:#5b626c}
.features{list-style:none;margin-top:2px}
.features li{font-size:7px;line-height:13px;color:#5b626c;padding-left:10px;position:relative}
.features li:before{content:"";position:absolute;left:1px;top:5px;width:3px;height:3px;background:var(--blue)}
.review{padding-bottom:5px}
.review + .review{border-top:1px solid var(--line);padding-top:5px}
.review-head{display:flex;align-items:center;gap:6px;font-size:7px;font-weight:700;color:var(--text)}
.review-head .stars{color:var(--star);font-size:8px}

/* sidebar */
.aside{left:503px;top:378px;width:262px}
.aside-head{height:22px;background:#3b4148;color:var(--white);font-size:11px;font-weight:700;text-align:center;line-height:22px}
.card{padding:9px 12px 6px}
.card-img{height:92px;background:radial-gradient(ellipse at 50% 55%,#2e5d9a 0%,#6e90bb 45%,#ffffff 75%)}
.card-name{text-align:center;font-size:8px;color:var(--text);margin:4px 0}
.card-sale{height:15px;background:var(--blue);color:var(--white);text-align:center;font-size:8px;font-weight:700;line-height:15px}
.card-meta{font-size:7px;line-height:11px;margin-top:5px;color:var(--muted)}
.card-meta b{color:var(--red);font-weight:700}
.card-meta .stars{color:var(--star)}
.card+.card{border-top:1px solid var(--line)}
.ebook{margin-top:6px;background:var(--panel);border-top:3px solid var(--blue);padding:8px 12px 10px}
.ebook h3{font-size:10px;font-weight:700;color:var(--blue-dark)}
.ebook p{font-size:7px;line-height:10px;color:#5b626c;margin-top:2px}
.ebook-form{display:flex;margin-top:6px}
.ebook-input{flex:1;height:18px;background:var(--white);border:1px solid var(--line);font-size:7px;color:var(--muted);line-height:16px;padding-left:5px}
.ebook-btn{width:62px;height:18px;background:var(--green);color:var(--white);font-size:7.5px;font-weight:700;text-align:center;line-height:18px}

/* newsletter */
.newsletter{left:124px;top:922px;width:641px;height:45px;background:var(--blue);display:flex;align-items:center;padding:0 10px;gap:10px}
.newsletter .icon{width:24px;height:24px;border-radius:50%;background:var(--white);display:flex;align-items:center;justify-content:center}
.newsletter h3{color:var(--white);font-size:13px;font-weight:700;flex:1}
.newsletter .input{width:190px;height:20px;background:var(--white);font-size:7.5px;color:var(--muted);line-height:20px;padding-left:6px}
.newsletter .btn{width:56px;height:20px;background:var(--green);color:var(--white);font-size:9px;font-weight:700;text-align:center;line-height:20px;margin-left:-10px}

/* footer */
.footer{left:0;top:1028px;width:889px;height:30px;background:var(--navy);display:flex;align-items:center;padding:0 124px}
.footer .label{color:var(--white);font-size:8px;font-weight:600}
.footer .input{width:120px;height:14px;background:var(--white);margin-left:8px}
.footer .btn{width:32px;height:14px;background:var(--blue);color:var(--white);font-size:7px;text-align:center;line-height:14px}
.footer .links{margin-left:auto;color:var(--white);font-size:8px;font-weight:600}
.legal{left:0;top:1066px;width:889px;text-align:center;font-size:7px;color:var(--muted);line-height:11px}
</style>
</head>
<body>

<header>
  <div class="abs brand"><span class="brand-mark"></span><span class="brand-name">HULLWRAP.COM</span></div>
  <div class="abs contact">
    <div class="contact-phone">
      <svg width="14" height="14" viewBox="0 0 24 24"><path fill="#1f63b0" d="M6.6 10.8a15.1 15.1 0 0 0 6.6 6.6l2.2-2.2c.3-.3.7-.4 1-.2 1.1.4 2.3.6 3.6.6.6 0 1 .4 1 1V20c0 .6-.4 1-1 1A17 17 0 0 1 3 4c0-.6.4-1 1-1h3.5c.6 0 1 .4 1 1 0 1.3.2 2.5.6 3.6.1.3 0 .7-.2 1z"/></svg>
      (800) 555-0148
    </div>
    <div class="contact-hours">Mon–Fri 9am to 6pm EST · Free Shipping</div>
  </div>
  <nav class="abs nav">
    <a>Boat Covers</a><a>Bass Boat Covers</a><a>T-Top Boat Covers</a><a>Bimini Tops</a><a>Jet Ski Covers</a>
    <span class="checkout">
      <svg width="10" height="10" viewBox="0 0 24 24"><path fill="#fff" d="M7 18a2 2 0 1 0 0 4 2 2 0 0 0 0-4zm10 0a2 2 0 1 0 0 4 2 2 0 0 0 0-4zM2 2h3l3.6 11.6h10l2.4-8H7"/></svg>
      CHECKOUT
    </span>
  </nav>
  <div class="abs crumbs">Home › Boat Covers › Center Console without Bow Rails › up to 15'6" Long and 84" Wide</div>
</header>

<div class="abs scene" role="img" aria-label="Sunny lake shoreline with blue sky, open water and sandy beach"></div>

<main class="abs sheet"></main>

<div class="abs gallery-main" role="img" aria-label="Grey fitted boat cover on a center console boat resting on a trailer"></div>
<div class="abs thumbs">
  <div class="thumb active" role="img" aria-label="Boat cover view"></div>
  <div class="thumb" role="img" aria-label="Boat cover view"></div>
  <div class="thumb" role="img" aria-label="Boat cover view"></div>
  <div class="thumb" role="img" aria-label="Boat cover view"></div>
  <div class="thumb" role="img" aria-label="Boat cover view"></div>
  <div class="thumb" role="img" aria-label="Boat cover view"></div>
  <div class="thumb" role="img" aria-label="Boat cover view"></div>
</div>

<section class="abs buy">
  <h1>Fits: Center Console without Bow Rails up to 15'6" Long and 84" Wide</h1>
  <div class="rating">★★★★★ <span>(5.0/5)</span></div>
  <div class="was">$600.00</div>
  <div class="sale">Our Sale: <b>50% Off</b></div>
  <div class="price">$300</div>
  <div class="field"><label>Color:</label><div class="select">Please Select</div></div>
  <div class="field"><label>Quantity:</label><div class="select">Please Select</div></div>
  <div class="cart">Add to Cart</div>
  <div class="share"><i></i><i></i><i></i><i></i></div>
</section>

<div class="abs info">
  <section class="section">
    <div class="section-bar">Product Info</div>
    <div class="section-body">
      <h2>Description:</h2>
      <p>When a boat is trailered or is exposed to harsh elements such as rain, dirt, sun, and UV, the Hullwrap cover is the most practical and durable protection. Its heavy fabric and tailored fit keep the hull, console and seats clean and dry. The 600 denier fabric is water resistant and breathable, keeping mildew away.</p>
      <h2 style="margin-top:8px">Features:</h2>
      <ul class="features">
        <li>5 Year Fit Guarantee for your boat size</li>
        <li>10 Year Warranty, Fabric stays strong and tight</li>
        <li>Fits snug around the console and seats</li>
        <li>The cover is 600 Denier solution dyed fabric</li>
        <li>Fabric is water resistant and breathable</li>
        <li>No sewing, just cinch the elastic hem</li>
        <li>Built to resist UV and mildew fading</li>
        <li>Free Shipping, you'll never pay more to order</li>
        <li>UV resistant and tear proof double stitched seams</li>
        <li>Four Trailerable straps included</li>
        <li>The front cover comes with an integrated vent</li>
        <li>Tough · Strong · Durable</li>
      </ul>
    </div>
  </section>

  <section class="section">
    <div class="section-bar">Reviews</div>
    <div class="section-body">
      <div class="review">
        <div class="review-head"><span class="stars">★★★★★</span>Fits like a glove</div>
        <p>Ordered for my 15 foot console boat and it fit perfectly. Straps held tight on a long highway trip.</p>
      </div>
      <div class="review">
        <div class="review-head"><span class="stars">★★★★☆</span>Great value</div>
        <p>Heavy fabric, easy to put on alone and it kept the seats dry through a rainy week at the lake.</p>
      </div>
    </div>
  </section>

  <section class="section">
    <div class="section-bar">Warranty</div>
    <div class="section-body">
      <p>Every cover carries a 10 year fabric warranty and a 5 year fit guarantee. If it does not fit your boat, we will replace it at no cost.</p>
    </div>
  </section>

  <section class="section">
    <div class="section-bar">Shipping</div>
    <div class="section-body">
      <p>Free shipping on every order. Most covers leave our warehouse within one business day and arrive in 3 to 5 days.</p>
    </div>
  </section>
</div>

<aside class="abs aside">
  <div class="aside-head">You may also like</div>
  <div class="card">
    <div class="card-img" role="img" aria-label="Blue boat cover fitted on a bass boat"></div>
    <div class="card-name">Harbor Runner 206</div>
    <div class="card-sale">ON SALE</div>
    <div class="card-meta">Best price: <b>$280</b><br>Free Shipping<br>Rating: <span class="stars">★★★★☆</span> (4/5)</div>
  </div>
  <div class="card">
    <div class="card-img" role="img" aria-label="Blue boat cover fitted on a runabout"></div>
    <div class="card-name">Harbor Runner 206</div>
    <div class="card-sale">ON SALE</div>
    <div class="card-meta">Best price: <b>$280</b><br>Free Shipping<br>Rating: <span class="stars">★★★★☆</span> (4/5)</div>
  </div>
  <div class="ebook">
    <h3>Free eBook: Boat Cover Care Guide</h3>
    <p>Tips to clean, store and extend the life of your cover. Sent straight to your inbox.</p>
    <div class="ebook-form"><span class="ebook-input">Enter your email address</span><span class="ebook-btn">Get eBook</span></div>
  </div>
</aside>

<section class="abs newsletter">
  <div class="icon">
    <svg width="14" height="14" viewBox="0 0 24 24"><path fill="none" stroke="#1f63b0" stroke-width="2.4" d="M3 6h18v12H3zM3 6l9 7 9-7"/></svg>
  </div>
  <h3>Subscribe to our Newsletter</h3>
  <div class="input">Enter your email address</div>
  <div class="btn">Sign Up</div>
</section>

<footer>
  <div class="abs footer">
    <span class="label">Sign Up To Win a FREE Boat Cover!</span>
    <span class="input"></span><span class="btn">Go</span>
    <span class="links">Exchanges &amp; Returns &nbsp;|&nbsp; Contact Us</span>
  </div>
  <div class="abs legal">Copyright © Hullwrap.com. All rights reserved.<br>Terms of Use · Privacy Policy · hullwrap.com</div>
</footer>

</body>
</html>
```